Brookvale Building Company - advertisement poster

I am looking to print some canvas signs to advertise my general contracting company, Brookvale Building Company. The sign will measure 6' long x 3' high so the size should match that ratio. I already have a logo icon, which is the Letter 'B' and some trees that I would like to incorporate, see attached. I would also like the to have the following information listed:
1) phone number: 831-555-0172
2) email: brookvalebuildingcompany@mailnest.example
3) website: brookvalebuildingcompany.example
4) Lic#4826130
5) I want to use this text: "BUILD WITH THE B-CREW!"

The ad should be relatively simple and clean. Black and Green are my company colors. I am open to creative ideas!

Target Market(s)

People looking to renovate their homes

Industry/Entity Type

Construction

Colors
59FF00
82FF00
B8FF75
E3FFCB
F4FFEA

Requirements
Must have
• Must have my company logo
Should not have
• No photos or complex graphics

```html
<!DOCTYPE html>
<html lang="en">
<head>
<meta charset="utf-8">
<title>Brookvale Building Company – Sign</title>
<link rel="stylesheet" href="https://fonts.googleapis.com/css2?family=Michroma&family=Poppins:wght@700;800&family=Roboto+Condensed:wght@400&display=swap">
<style>
  :root {
    --ink: #1b1b1b;
    --paper: #ffffff;
    --green: #64a844;
    --stage: #e9e9e9;
  }
  * { margin: 0; padding: 0; box-sizing: border-box; }
  html, body { width: 1200px; height: 635px; overflow: hidden; background: var(--stage); }
  .sign {
    position: absolute; left: 30px; top: 32px;
    width: 1140px; height: 570px;
    background: var(--ink);
  }
  .headline-band {
    position: absolute; left: 0; top: 0; width: 1140px; height: 261px;
    background: var(--paper);
  }
  .headline { position: absolute; left: 0; top: 0; width: 1140px; height: 261px; }
  .headline text { font-family: "Michroma", sans-serif; }
  .brand {
    position: absolute; left: 60px; top: 320px; width: 420px;
    display: flex; flex-direction: column; align-items: center; gap: 22px;
  }
  .brand-mark { width: 70px; height: 70px; background: var(--green); }
  .brand-name {
    font-family: "Michroma", sans-serif; color: var(--paper);
    font-size: 25px; line-height: 1.35; text-align: center; letter-spacing: 1px;
    text-transform: uppercase;
  }
  .contact { position: absolute; left: 508px; top: 0; }
  .contact-row { position: absolute; left: 0; display: flex; align-items: center; white-space: nowrap; }
  .contact-icon { width: 34px; height: 34px; flex: none; margin-right: 14px; }
  .phone { top: 318px; }
  .phone .contact-value { font-family: "Poppins", sans-serif; font-weight: 800; font-size: 50px; color: var(--paper); line-height: 1; }
  .email { top: 374px; }
  .web { top: 422px; }
  .email .contact-value, .web .contact-value {
    font-family: "Roboto Condensed", sans-serif; font-size: 31px; color: var(--paper); line-height: 1;
  }
  .web .accent { color: var(--green); }
  .license { position: absolute; left: 14px; top: 470px; width: 477px; height: 43px; }
</style>
</head>
<body>
<div class="sign">
  <div class="headline-band"></div>
  <svg class="headline" viewBox="0 0 1140 261" aria-label="Build with the B-Crew!">
    <text x="76" y="132" font-size="100" fill="#1b1b1b" textLength="827" lengthAdjust="spacingAndGlyphs">BUILD WITH</text>
    <text x="73" y="240" font-size="110" fill="#64a844" textLength="991" lengthAdjust="spacingAndGlyphs">THE B-CREW!</text>
  </svg>

  <div class="brand">
    <div class="brand-mark"></div>
    <div class="brand-name">Brookvale<br>Building Company</div>
  </div>

  <div class="contact">
    <div class="contact-row phone">
      <svg class="contact-icon" viewBox="0 0 34 34" aria-hidden="true">
        <circle cx="17" cy="17" r="17" fill="#64a844"/>
        <path d="M11 9c1-1 2-1 3 0l2 3c.5 1 .3 1.7-.5 2.4l-1 .9c.9 2 2.3 3.5 4.3 4.4l.9-1c.7-.8 1.5-1 2.4-.5l3 2c1 .8 1 1.9 0 2.9l-1.3 1.3c-1.3 1.3-4 1-7-1.2-3.4-2.5-6-5.7-7-8.8-.6-2-.5-3.6.5-4.6z" fill="#fff"/>
      </svg>
      <span class="contact-value">831-555-0172</span>
    </div>
    <div class="contact-row email">
      <svg class="contact-icon" viewBox="0 0 34 34" aria-hidden="true">
        <circle cx="17" cy="17" r="17" fill="#64a844"/>
        <rect x="8" y="11" width="18" height="12" fill="#fff"/>
        <path d="M8 11l9 7 9-7" fill="none" stroke="#64a844" stroke-width="1.6"/>
      </svg>
      <span class="contact-value">brookvalebuildingcompany@mailnest.example</span>
    </div>
    <div class="contact-row web">
      <svg class="contact-icon" viewBox="0 0 34 34" aria-hidden="true">
        <circle cx="17" cy="17" r="17" fill="#64a844"/>
        <g fill="none" stroke="#fff" stroke-width="1.6">
          <circle cx="17" cy="17" r="9"/>
          <ellipse cx="17" cy="17" rx="4" ry="9"/>
          <path d="M8 17h18M9.5 12.5h15M9.5 21.5h15"/>
        </g>
      </svg>
      <span class="contact-value">www.<span class="accent">brookvalebuildingcompany</span>.example</span>
    </div>
    <svg class="license" viewBox="0 0 477 43" aria-label="License #4826130">
      <polygon points="0,0 247,0 268,43 20,43" fill="#64a844"/>
      <polygon points="247,0 457,0 477,43 268,43" fill="#ffffff"/>
      <text x="54" y="31" font-family="Poppins, sans-serif" font-weight="700" font-size="25" letter-spacing="6" fill="#ffffff">LICENSE</text>
      <text x="262" y="31" font-family="Poppins, sans-serif" font-weight="800" font-size="26" letter-spacing="4" fill="#1b1b1b">#4826130</text>
    </svg>
  </div>
</div>
</body>
</html>
```